Trailhead Cove Website - Sell Outdoor product

We are a mom and pop company that just opened our website.

We need a fresh, professional, and nice looking website for our outdoor products. We sell hunting, camping, fishing, and hiking products/accessories to name a few. Some of these products are optics, gun safes, gun bi-pods and tripods, gun lights, hunting camera, tents, hearing protection, targets, fishing poles, and hiking backpacks to name a few.

Our current website is: http://www.trailheadcove-example.com . You'll see our logo on the website, and it is attached. We aren't married to this logo, so if the designer thinks they can modify it or even come up with a better design for the website, they are more than welcome to do so. We need someone with good images of their own (clip art and/or outdoor images) they can use if they need to for our website.

I also attached a idea I had in plandraw, but please don't think this is set in stone. It is just a very rough idea. You can also go to our bazarro site to see what we sell: www.bazarro-example.com/shops/k9qz311mrtxn4p . Right now we sell everything on Bazarro, but our website will just focus on outdoor product. So please make it an outdoor focused website. And you can be creative with some of the product category names. We also want to leave room for some parallel product in the future. Like garden tools, back yard furniture, and BBQs.

Our company also wants to include a deals section on the website. We will probably update it once a week or month. I have included what I did for a deal and accompanying images for it. Image is called Morvelid (And the main images are 01 and 02).

We also want to make sure the file is compatible with our current web-hosting company, https://www.hostlyne-example.com. So I included a webpage layout zip folder. If you have any questions, please contact me.

This is for a PSD and HTML/CSS webpage. If you have any artwork or images that you own and want to use them for the webpage, please do so.

Target Market(s)

The hunter, outdoors person, camper, hiker, and etc.

Industry/Entity Type

It Company

Coding

Coded - Design and coding required

Number of Pages Required

3 page

Requirements
Must have
• The main page. PSD and HTML/CSS file.
• The category page. PSD and HTML/CSS file
• The product display page. PSD and HTML/CSS file
• Please also use some images that you have or from the sites below:
• You can get free stock images for 7 days (20 per day) from this site:
• https://www.pixelvault-example.com/complimentary/PVXTRL/?utm_source=PVXTrialFT&utm_medium=cpc&utm_campaign=PVXTrialFT&gclid=QWRt5mnBkdTRZpLoWsePb7uVbQ
• Has 14 good sites:
• http://www.venturedesk-example.com/article/517293
• Here are the ones I like:
• https://clearshot-example.com/
• http://brightwide-example.com/
• http://www.sitebloom-example.com/free/nature
• http://www.pictorium-example.com/archive
• http://tinyframes-example.co/
• http://old.vintlens-example.co/search/hiking
• http://fetchpix.blogsite-example.com/
• http://rolvenpask-example.com/post/584920173645/download
• http://openimagevault-example.com/
• If there is a photographer listed on or next to the image, on the bottom lower corner of the image, please put the photographer's name.
Nice to have
• I would like to have an unsubscribe page. If the designer has any of their own images of the outdoor world, and they want to use them, please do. Just make the right graphic changes to make it look good.
Should not have
• Try and keep green color to a minimum.

```html
<!DOCTYPE html>
<html lang="en">
<head>
<meta charset="utf-8">
<title>Trailhead Cove — Outdoor Gear</title>
<link href="https://fonts.googleapis.com/css2?family=Open+Sans:wght@400;600;700;800&display=swap" rel="stylesheet">
<style>
:root{
  --yellow:#fbbc10;
  --yellow-dark:#e0a500;
  --black:#0b0b0b;
  --ink:#222;
  --grey-text:#666;
  --strike:#a5a5a5;
  --line:#e3e3e3;
  --section-bg:#f6f6f6;
  --footer-bg:#0d0d0d;
  --footer-bottom:#050505;
  --footer-text:#9a9a9a;
  --green:#27b43b;
}
*{box-sizing:border-box;margin:0;padding:0}
html,body{width:1200px;height:2161px;overflow:hidden}
body{font-family:"Open Sans",Arial,sans-serif;color:var(--ink);background:#fff;position:relative}
ul{list-style:none}

/* top bar */
.topbar{height:40px;border-top:3px solid var(--black);border-bottom:1px solid var(--line);position:relative;background:#fff}
.newsletter-btn{position:absolute;left:98px;top:0;width:186px;height:37px;background:var(--yellow);color:#fff;font-size:12px;font-weight:700;display:flex;align-items:center;justify-content:center;gap:8px;letter-spacing:.2px}
.account-links{position:absolute;right:98px;top:0;height:37px;display:flex;align-items:center;gap:12px;font-size:11px;font-weight:600;color:#222}
.account-links span.sep{color:#444}
.account-links .link{display:flex;align-items:center;gap:6px}

/* header */
.brand-header{height:140px;display:flex;align-items:center;justify-content:center;background:#fff}
.brand-name{display:flex;align-items:center;gap:12px;font-size:38px;font-weight:800;color:var(--black);letter-spacing:.5px;text-transform:uppercase}
.brand-name .mark{width:26px;height:26px;border-radius:50%;background:var(--yellow)}

/* nav */
.main-nav{height:50px;background:linear-gradient(#1a1a1a,#000);position:relative}
.main-nav ul{position:absolute;left:300px;right:98px;top:0;height:50px;display:flex;align-items:center;justify-content:space-between}
.main-nav li{font-size:12px;font-weight:700;color:#fff;padding:0 20px;height:22px;line-height:22px;border-left:1px solid #3a3a3a}
.main-nav li:first-child{border-left:none;color:var(--yellow);padding-left:24px}
.main-nav li:last-child{padding-right:0}

/* side category menu */
.category-menu{position:absolute;left:98px;top:180px;width:202px;z-index:5}
.category-menu ul{background:linear-gradient(var(--yellow),var(--yellow-dark))}
.category-menu li{height:44.6px;line-height:44.6px;text-align:center;color:#fff;font-size:13.5px;font-weight:700;border-bottom:1px solid rgba(255,255,255,.25)}
.category-menu li:first-child{height:50px;line-height:58px}
.category-menu li:last-child{border-bottom:none}
.category-menu svg{display:block}

/* hero */
.hero{position:relative;height:444px;background:linear-gradient(100deg,#7d8ea6 0%,#c9d6e6 22%,#5c82b8 40%,#d8e2ee 55%,#8a6a58 72%,#5b3f31 100%)}
.hero .photo{position:absolute;inset:0}
.hero-copy{position:absolute;left:353px;top:70px;color:#fff}
.hero-copy h1{font-size:35px;font-weight:800;letter-spacing:2px;text-transform:uppercase}
.hero-copy p{font-size:16px;line-height:20px;margin-top:6px;width:350px;color:#f1f1f1}
.read-more{display:inline-block;margin-top:24px;width:104px;height:37px;border:2px solid #111;border-radius:20px;background:rgba(255,255,255,.55);font-size:12px;font-weight:700;color:#111;text-align:center;line-height:33px}
.hero-dots{position:absolute;left:562px;top:418px;display:flex;gap:3px}
.hero-dots i{width:9px;height:9px;border-radius:50%;background:#fff;display:block}
.hero-dots i.active{background:var(--yellow)}

/* products */
.new-products{background:var(--section-bg);height:748px;padding-top:26px}
.section-title{text-align:center;font-size:22px;font-weight:700;color:#222;text-transform:uppercase}
.product-grid{width:1004px;margin:16px auto 0;display:grid;grid-template-columns:repeat(5,179px);justify-content:space-between;row-gap:26px}
.product-card{height:300px;background:#fff;border:1px solid var(--line);position:relative;overflow:hidden}
.product-photo{position:absolute;left:30px;top:14px;width:118px;height:118px;border-radius:6px}
.ribbon{position:absolute;left:0;top:0;width:0;height:0;border-top:58px solid var(--green);border-right:58px solid transparent}
.ribbon span{position:absolute;left:4px;top:-48px;transform:rotate(-45deg);color:#fff;font-size:11px;font-weight:700}
.product-name{position:absolute;top:177px;left:0;right:0;text-align:center;font-size:12.5px;font-weight:700;color:#222}
.product-desc{position:absolute;top:211px;left:18px;right:18px;text-align:center;font-size:10.5px;line-height:16px;color:#555}
.price-bar{position:absolute;left:0;right:0;bottom:0;height:37px;border-top:1px solid var(--line);display:flex}
.price{flex:1;display:flex;align-items:center;justify-content:center;gap:6px;font-size:13px;font-weight:700}
.price s{color:var(--strike)}
.price b{color:var(--yellow)}
.cart-btn{width:44px;border-left:1px solid var(--line);display:flex;align-items:center;justify-content:center}
.product-card.featured .price{background:#2a2a2a}
.product-card.featured .price s{color:#fff;text-decoration:none}
.product-card.featured .cart-btn{background:var(--yellow);border-left:none}

/* blog */
.blog{height:368px;background:#fff;padding-top:30px}
.blog-grid{width:1004px;margin:20px auto 0;display:grid;grid-template-columns:repeat(3,315px);justify-content:space-between}
.blog-photo{height:157px;border:1px solid #ccc}
.blog-date{margin-top:12px;font-size:13px;font-weight:700;color:var(--yellow)}
.blog-text{margin-top:6px;font-size:12px;line-height:19px;color:#444}

/* footer */
.site-footer{height:307px;background:var(--footer-bg);position:relative;color:var(--footer-text)}
.footer-col{position:absolute;top:34px}
.footer-col h3{font-size:13.5px;font-weight:700;color:var(--yellow);text-transform:uppercase}
.footer-col p,.footer-col li{font-size:11.5px;line-height:21.5px}
.col-about{left:99px;width:168px}
.col-about p{margin-top:14px;line-height:19px}
.col-about h3.follow{margin-top:46px}
.social{display:flex;gap:8px;margin-top:16px}
.social i{width:24px;height:24px;border-radius:50%;display:block}
.col-terms{left:390px;width:200px}
.col-terms ul{margin-top:14px}
.col-contact{left:660px;width:220px}
.contact-row{display:flex;gap:16px;margin-top:14px;font-size:11.5px;line-height:19px}
.contact-row + .contact-row{margin-top:26px}
.subscribe{margin-top:34px;display:flex;width:192px;height:33px}
.subscribe span{flex:1;background:#fff;color:#555;font-size:11px;line-height:33px;padding-left:10px}
.subscribe b{width:35px;background:var(--yellow);display:flex;align-items:center;justify-content:center}
.col-shipping{left:965px;width:140px}
.col-shipping ul{margin-top:14px}
.divider{position:absolute;top:72px;width:1px;height:200px;background:#1f1f1f}

.footer-bottom{height:64px;background:var(--footer-bottom);position:relative;color:#a0a0a0;font-size:11px}
.footer-links{position:absolute;left:99px;top:0;line-height:64px;display:flex;gap:10px}
.copyright{position:absolute;left:492px;top:0;line-height:64px;font-size:10.5px;color:#888}
.help-btn{position:absolute;left:905px;top:13px;width:197px;height:38px;background:var(--yellow);border-radius:3px;color:#fff;font-size:13px;font-weight:700;text-align:center;line-height:38px}
</style>
</head>
<body>

<div class="topbar">
  <div class="newsletter-btn">JOIN OUR NEWSLETTER
    <svg width="16" height="11" viewBox="0 0 16 11"><rect x=".5" y=".5" width="15" height="10" fill="#fff"/><path d="M1 1l7 5 7-5" stroke="#fbbc10" stroke-width="1.4" fill="none"/></svg>
  </div>
  <div class="account-links">
    <span class="link"><svg width="10" height="11" viewBox="0 0 10 11"><circle cx="5" cy="3" r="2.6" fill="#222"/><path d="M0 11c0-4 2-5 5-5s5 1 5 5z" fill="#222"/></svg>MY ACCOUNT</span><span class="sep">|</span>
    <span class="link"><svg width="9" height="11" viewBox="0 0 9 11"><rect y="5" width="9" height="6" fill="#222"/><path d="M2 5V3a2.5 2.5 0 0 1 5 0" stroke="#222" stroke-width="1.5" fill="none"/></svg>LOGIN</span><span class="sep">|</span>
    <span class="link"><svg width="13" height="11" viewBox="0 0 13 11"><path d="M0 1h2.5l2 6h7l1.5-5H4" stroke="#222" stroke-width="1.5" fill="none"/><circle cx="5" cy="9.5" r="1.2" fill="#222"/><circle cx="10" cy="9.5" r="1.2" fill="#222"/></svg>SHOPPING CART</span>
  </div>
</div>

<header class="brand-header">
  <div class="brand-name"><i class="mark"></i>Trailhead Cove</div>
</header>

<nav class="main-nav">
  <ul>
    <li>HOME</li><li>HUNTINGACCESSORIES</li><li>CAMPING</li><li>FISHING</li><li>HIKING</li><li>THIS WEEKSDEALS</li><li>BRANDS</li>
  </ul>
</nav>

<aside class="category-menu">
  <ul>
    <li>OPTICS</li><li>SAFES</li><li>BIPOD AND TRIPODS</li><li>LIGHTS</li><li>BRANDS</li><li>CAMERAS</li><li>TENTS</li><li>EAR PROTECTION</li><li>TARGETS</li>
  </ul>
  <svg width="202" height="62" viewBox="0 0 202 62"><polygon points="0,0 202,0 202,62 101,22 0,62" fill="#e0a500"/><polyline points="0,56 101,16 202,56" stroke="#111" stroke-width="4" fill="none"/></svg>
</aside>

<section class="hero">
  <div class="photo" role="img" aria-label="Hiker with a red jacket and backpack climbing a rocky trail below snowy mountain peaks"></div>
  <div class="hero-copy">
    <h1>Trailhead Cove</h1>
    <p>Sed ut perspiciatis unde omnis iste natus error sit voluptatem accusantium doloremque.</p>
    <span class="read-more">READ MORE</span>
  </div>
  <div class="hero-dots"><i></i><i></i><i></i><i class="active"></i><i></i><i></i></div>
</section>

<section class="new-products">
  <h2 class="section-title">New Products</h2>
  <div class="product-grid">
    <div class="product-card"><div class="product-photo" role="img" aria-label="Blue ear protection muffs" style="background:radial-gradient(circle,#2f5fa8,#dfe6ef 70%)"></div><div class="ribbon"><span>NEW</span></div><div class="product-name">PRODUCT NAME</div><div class="product-desc">Kestrel Guard Ridgeline 9 Hea-ring Protector.</div><div class="price-bar"><div class="price"><s>$89.40</s><b>$60.78</b></div><div class="cart-btn"><svg width="13" height="11" viewBox="0 0 13 11"><path d="M0 1h2.5l2 6h7l1.5-5H4z" fill="#333"/><circle cx="5" cy="9.5" r="1.2" fill="#333"/><circle cx="10" cy="9.5" r="1.2" fill="#333"/></svg></div></div></div>
    <div class="product-card"><div class="product-photo" role="img" aria-label="Black rifle bipod" style="background:radial-gradient(circle,#333,#eee 70%)"></div><div class="product-name">PRODUCT NAME</div><div class="product-desc">Kestrel Guard Ridgeline 9 Hea-ring Protector.</div><div class="price-bar"><div class="price"><s>$89.40</s><b>$60.78</b></div><div class="cart-btn"><svg width="13" height="11" viewBox="0 0 13 11"><path d="M0 1h2.5l2 6h7l1.5-5H4z" fill="#333"/><circle cx="5" cy="9.5" r="1.2" fill="#333"/><circle cx="10" cy="9.5" r="1.2" fill="#333"/></svg></div></div></div>
    <div class="product-card featured"><div class="product-photo" role="img" aria-label="Packaged set of batteries" style="background:radial-gradient(circle,#555,#e8e8e8 70%)"></div><div class="product-name">PRODUCT NAME</div><div class="product-desc">Kestrel Guard Ridgeline 9 Hea-ring Protector.</div><div class="price-bar"><div class="price"><s>$89.40</s><b>$60.78</b></div><div class="cart-btn"><svg width="13" height="11" viewBox="0 0 13 11"><path d="M0 1h2.5l2 6h7l1.5-5H4z" fill="#fff"/><circle cx="5" cy="9.5" r="1.2" fill="#fff"/><circle cx="10" cy="9.5" r="1.2" fill="#fff"/></svg></div></div></div>
    <div class="product-card"><div class="product-photo" role="img" aria-label="Small black flashlight with clip" style="background:radial-gradient(circle,#222,#eee 65%)"></div><div class="product-name">PRODUCT NAME</div><div class="product-desc">Kestrel Guard Ridgeline 9 Hea-ring Protector.</div><div class="price-bar"><div class="price"><s>$89.40</s><b>$60.78</b></div><div class="cart-btn"><svg width="13" height="11" viewBox="0 0 13 11"><path d="M0 1h2.5l2 6h7l1.5-5H4z" fill="#333"/><circle cx="5" cy="9.5" r="1.2" fill="#333"/><circle cx="10" cy="9.5" r="1.2" fill="#333"/></svg></div></div></div>
    <div class="product-card"><div class="product-photo" role="img" aria-label="Black multi-tool spork" style="background:radial-gradient(circle,#2a2a2a,#eee 65%)"></div><div class="product-name">PRODUCT NAME</div><div class="product-desc">Kestrel Guard Ridgeline 9 Hea-ring Protector.</div><div class="price-bar"><div class="price"><s>$89.40</s><b>$60.78</b></div><div class="cart-btn"><svg width="13" height="11" viewBox="0 0 13 11"><path d="M0 1h2.5l2 6h7l1.5-5H4z" fill="#333"/><circle cx="5" cy="9.5" r="1.2" fill="#333"/><circle cx="10" cy="9.5" r="1.2" fill="#333"/></svg></div></div></div>

    <div class="product-card"><div class="product-photo" role="img" aria-label="Red dot sight" style="background:radial-gradient(circle,#d88a1a,#222 35%,#eee 70%)"></div><div class="product-name">PRODUCT NAME</div><div class="product-desc">Kestrel Guard Ridgeline 9 Hea-ring Protector.</div><div class="price-bar"><div class="price"><s>$89.40</s><b>$60.78</b></div><div class="cart-btn"><svg width="13" height="11" viewBox="0 0 13 11"><path d="M0 1h2.5l2 6h7l1.5-5H4z" fill="#333"/><circle cx="5" cy="9.5" r="1.2" fill="#333"/><circle cx="10" cy="9.5" r="1.2" fill="#333"/></svg></div></div></div>
    <div class="product-card"><div class="product-photo" role="img" aria-label="Cartridge-shaped pocket flashlight" style="background:radial-gradient(circle,#333,#c9a064 40%,#eee 70%)"></div><div class="product-name">PRODUCT NAME</div><div class="product-desc">Kestrel Guard Ridgeline 9 Hea-ring Protector.</div><div class="price-bar"><div class="price"><s>$89.40</s><b>$60.78</b></div><div class="cart-btn"><svg width="13" height="11" viewBox="0 0 13 11"><path d="M0 1h2.5l2 6h7l1.5-5H4z" fill="#333"/><circle cx="5" cy="9.5" r="1.2" fill="#333"/><circle cx="10" cy="9.5" r="1.2" fill="#333"/></svg></div></div></div>
    <div class="product-card"><div class="product-photo" role="img" aria-label="Black rifle scope" style="background:radial-gradient(circle,#1e1e1e,#eee 65%)"></div><div class="ribbon"><span>NEW</span></div><div class="product-name">PRODUCT NAME</div><div class="product-desc">Kestrel Guard Ridgeline 9 Hea-ring Protector.</div><div class="price-bar"><div class="price"><s>$89.40</s><b>$60.78</b></div><div class="cart-btn"><svg width="13" height="11" viewBox="0 0 13 11"><path d="M0 1h2.5l2 6h7l1.5-5H4z" fill="#333"/><circle cx="5" cy="9.5" r="1.2" fill="#333"/><circle cx="10" cy="9.5" r="1.2" fill="#333"/></svg></div></div></div>
    <div class="product-card"><div class="product-photo" role="img" aria-label="Blue ear protection muffs" style="background:radial-gradient(circle,#2f5fa8,#dfe6ef 70%)"></div><div class="product-name">PRODUCT NAME</div><div class="product-desc">Kestrel Guard Ridgeline 9 Hea-ring Protector.</div><div class="price-bar"><div class="price"><s>$89.40</s><b>$60.78</b></div><div class="cart-btn"><svg width="13" height="11" viewBox="0 0 13 11"><path d="M0 1h2.5l2 6h7l1.5-5H4z" fill="#333"/><circle cx="5" cy="9.5" r="1.2" fill="#333"/><circle cx="10" cy="9.5" r="1.2" fill="#333"/></svg></div></div></div>
    <div class="product-card"><div class="product-photo" role="img" aria-label="Open black handgun safe" style="background:radial-gradient(circle,#1a1a1a,#eee 70%)"></div><div class="product-name">PRODUCT NAME</div><div class="product-desc">Kestrel Guard Ridgeline 9 Hea-ring Protector.</div><div class="price-bar"><div class="price"><s>$89.40</s><b>$60.78</b></div><div class="cart-btn"><svg width="13" height="11" viewBox="0 0 13 11"><path d="M0 1h2.5l2 6h7l1.5-5H4z" fill="#333"/><circle cx="5" cy="9.5" r="1.2" fill="#333"/><circle cx="10" cy="9.5" r="1.2" fill="#333"/></svg></div></div></div>
  </div>
</section>

<section class="blog">
  <h2 class="section-title">Recent Blog News</h2>
  <div class="blog-grid">
    <article><div class="blog-photo" role="img" aria-label="Two hikers with trekking poles on a mountain ridge" style="background:linear-gradient(#6d9ad0,#a9c3e0 55%,#7c7a68)"></div><div class="blog-date">20 MARCH 2015</div><p class="blog-text">At vero eos et accusamus et iusto odio dignissimos ducimus qui blanditiis praesentium voluptatum deleniti atque corrupti quos dolores</p></article>
    <article><div class="blog-photo" role="img" aria-label="Hunter in orange vest with a dog in a tall grass field" style="background:linear-gradient(#8b7a52,#a38d5c 50%,#6c5a39)"></div><div class="blog-date">20 MARCH 2015</div><p class="blog-text">At vero eos et accusamus et iusto odio dignissimos ducimus qui blanditiis praesentium voluptatum deleniti atque corrupti quos dolores</p></article>
    <article><div class="blog-photo" role="img" aria-label="Angler casting a fishing rod at sunset over water" style="background:linear-gradient(160deg,#3b3226,#d88a2e 55%,#f3c46a 70%,#2b2218)"></div><div class="blog-date">20 MARCH 2015</div><p class="blog-text">At vero eos et accusamus et iusto odio dignissimos ducimus qui blanditiis praesentium voluptatum deleniti atque corrupti quos dolores</p></article>
  </div>
</section>

<footer class="site-footer">
  <div class="footer-col col-about">
    <h3>About Us</h3>
    <p>At vero eos et accusamus et iusto odio dignissimos ducimus qui blanditiis praesentium voluptatum deleniti atque cor-rupti quos dolores.</p>
    <h3 class="follow">Follow Us</h3>
    <div class="social"><i style="background:#3b5998"></i><i style="background:#1da1f2"></i><i style="background:#f2b400"></i><i style="background:#d01f2a"></i></div>
  </div>
  <span class="divider" style="left:350px"></span>
  <div class="footer-col col-terms">
    <h3>Terms &amp; Conditions</h3>
    <ul><li>Microscopes</li><li>Riflescopes</li><li>Safe</li><li>Shooting accessories</li><li>Spotting Scopes</li><li>Telescopes</li><li>View all categories</li><li>Binoculars</li><li>Metal Detectors</li></ul>
  </div>
  <span class="divider" style="left:586px"></span>
  <div class="footer-col col-contact">
    <h3>Contact Us</h3>
    <div class="contact-row"><svg width="18" height="16" viewBox="0 0 18 16"><path d="M9 1L1 8h2.5v7h4v-4h3v4h4V8H17z" fill="#9a9a9a"/></svg><span>4120 Ridgeback Lane,<br>Pinewood, DC 45 Fr 45.</span></div>
    <div class="contact-row"><svg width="18" height="16" viewBox="0 0 18 16"><rect x="5" y="0" width="8" height="16" rx="1.5" fill="#9a9a9a"/><rect x="6.5" y="2" width="5" height="10" fill="#0d0d0d"/></svg><span>Telephone: +1 5550 142 377<br>FAX: +1 555 018 4421</span></div>
    <div class="subscribe"><span>Enter your email..</span><b><svg width="16" height="11" viewBox="0 0 16 11"><rect x=".5" y=".5" width="15" height="10" fill="#fff"/><path d="M1 1l7 5 7-5" stroke="#fbbc10" stroke-width="1.4" fill="none"/></svg></b></div>
  </div>
  <span class="divider" style="left:905px"></span>
  <div class="footer-col col-shipping">
    <h3>Shipping&amp; Return</h3>
    <ul><li>Praesent vestibulumean</li><li>Nonummy hendrerit</li><li>maurissce suscipit</li><li>Aarius miraesent ves</li><li>bulum aenean</li><li>Nonummy hendrerit</li><li>Fusce suscipit varius mi</li></ul>
  </div>
</footer>

<div class="footer-bottom">
  <div class="footer-links"><span>HOME</span>|<span>ABOUT US</span>|<span>FAQ</span>|<span>BLOG</span>|<span>PRIVACY</span></div>
  <div class="copyright">© 2015 TRAILHEAD COVE LLC. ALL RIGHTS RESERVED</div>
  <div class="help-btn">NEED HELP:(555) 014-2290</div>
</div>

</body>
</html>
```